Essential oil label for bottles

Looking to modify our current logo and label design. It looks too simple. I will attach images of our competitors to use as examples. Our company name is Velunta. We have 2 different bottles. Clear and amber color. Going forward, we will be using only the amber bottle. The other 2 images are the biggest sellers brands. We want to make some adjustments to ours.

Target Market(s)

Brindex sales

Industry/Entity Type

Essential oil, perfume

Colors

Designer to choose only greyscale colors for use in the design.

Requirements
Nice to have
• A slight change to fonts and logo design. Maybe change the font and design of the word "Velunta" in our logo. Maybe add something to the label to make it stand out more but still keeping it clean and modern
Should not have
• No colors, besides, black, grays, whites, and off white.

```html
<!DOCTYPE html>
<html lang="en">
<head>
<meta charset="utf-8">
<title>Velunta Fragrance Oil Labels</title>
<link href="https://fonts.googleapis.com/css2?family=Lexend:wght@300;400;600&display=swap" rel="stylesheet">
<style>
  :root {
    --backdrop: #f8f6f1;
    --ink: #121212;
    --paper: #f4f4f4;
    --band-light: #e6e6e6;
    --rule-dark: #8a8a8a;
    --rule-light: #3a3a3a;
    --muted-dark: #c9c9c9;
    --muted-light: #555555;
    --chip-light: #d4d4d4;
  }
  * { margin: 0; padding: 0; box-sizing: border-box; }
  html, body {
    width: 1200px; height: 800px; overflow: hidden;
    background: var(--backdrop);
    font-family: "Lexend", sans-serif;
  }
  .canvas {
    width: 1200px; height: 800px;
    display: flex; justify-content: center; align-items: center;
    gap: 100px;
  }
  .label {
    position: relative;
    width: 300px; height: 431px;
    display: flex; flex-direction: column;
  }
  .label__body { flex: 1; padding: 46px 0 0 35px; }
  .label__title {
    font-size: 23px; letter-spacing: 0.02em; line-height: 1;
    font-weight: 600;
  }
  .label__title .light { font-weight: 300; }
  .label__type {
    margin-top: 11px; font-size: 12px; font-weight: 300;
    letter-spacing: 0.03em;
  }
  .label__rule { margin-top: 10px; width: 194px; height: 1px; }
  .label__notes {
    margin-top: 9px; font-size: 10.5px; font-weight: 300;
    display: flex; align-items: center; gap: 3px; letter-spacing: 0.01em;
  }
  .label__notes .sep { width: 1px; height: 14px; }
  .label__notes .note { padding: 1px 3px; }
  .label__volume { margin-top: 10px; font-size: 8px; font-weight: 300; }
  .label__brand-band {
    height: 32px; display: flex; align-items: center; justify-content: center;
    font-size: 10px; font-weight: 400; letter-spacing: 0.55em;
    padding-left: 0.55em;
  }
  .label__foot-band { height: 26px; }

  .label--dark { background: var(--ink); color: #ffffff; }
  .label--dark .label__type { color: var(--muted-dark); }
  .label--dark .label__rule, .label--dark .sep { background: var(--rule-dark); }
  .label--dark .note--active { background: var(--chip-light); color: var(--ink); }
  .label--dark .label__brand-band { background: var(--band-light); color: var(--ink); }
  .label--dark .label__foot-band { background: var(--ink); }

  .label--light { background: var(--paper); color: var(--ink); }
  .label--light .label__type { color: var(--muted-light); }
  .label--light .label__volume { color: #8c8c8c; }
  .label--light .label__rule, .label--light .sep { background: var(--rule-light); }
  .label--light .note--active { background: var(--ink); color: #ffffff; }
  .label--light .label__brand-band { background: var(--ink); color: #ffffff; }
  .label--light .label__foot-band { background: var(--band-light); }
</style>
</head>
<body>
<main class="canvas">
  <section class="label label--dark">
    <div class="label__body">
      <h1 class="label__title">PALOSANTO</h1>
      <p class="label__type">FRAGRANCE OIL</p>
      <div class="label__rule"></div>
      <p class="label__notes">
        <span class="note">WHITETEA</span><span class="sep"></span>
        <span class="note">ORANGE</span>
        <span class="note note--active">PALOSANTO</span>
      </p>
      <p class="label__volume">200 ML</p>
    </div>
    <div class="label__brand-band">VELUNTA</div>
    <div class="label__foot-band"></div>
  </section>

  <section class="label label--light">
    <div class="label__body">
      <h1 class="label__title">WHITE <span class="light">TEA</span></h1>
      <p class="label__type">FRAGRANCE OIL</p>
      <div class="label__rule"></div>
      <p class="label__notes">
        <span class="note note--active">WHITETEA</span>
        <span class="note">ORANGE</span><span class="sep"></span>
        <span class="note">PALOSANTO</span>
      </p>
      <p class="label__volume">200 ML</p>
    </div>
    <div class="label__brand-band">VELUNTA</div>
    <div class="label__foot-band"></div>
  </section>
</main>
</body>
</html>
```